Anzeigengestaltung für eine Hausarztpraxis
Zielgruppe
Wir sind eine Hausarztpraxis mit zwei Standorten und suchen eine Ärztin oder einen Arzt zur Anstellung in der klassischen Hausarzt Medizin am Standort Talwil
Aufgabenstellung
Bitte beachtet den Text im Anhang, der ist schon vorgegeben. (Anzeigentext)
Wir suchen ein ruhiges, hochwertiges Layout für eine Stellenanzeige einer Hausarztpraxis in einem historischen Gebäude.
Der Text steht im Vordergrund, das Design soll zurückhaltend, klar und wertig sein.
Bitte keine Icons, keine bunten Farben, keine verspielten Elemente.
Gerne viel Weissraum, klare Typografie, ruhige Anmutung.
Schrift: Garamond für den Fliesstext (bereits gewählt).
Das Layout soll sowohl als PDF wie auch online funktionieren.
Optional: ein sehr dezentes grafisches Element oder eine ruhige Bildanmutung (z. B. Struktur, Licht, Architekturdetail).

```html
<!DOCTYPE html>
<html lang="de">
<head>
<meta charset="utf-8">
<title>Stellenanzeige – Praxis Lindenhof</title>
<link href="https://fonts.googleapis.com/css2?family=EB+Garamond:wght@400;500;600&family=Open+Sans:ital,wght@1,400&family=Sora:wght@600;700&display=swap" rel="stylesheet">
<style>
  :root {
    --stage: #e6e6e6;
    --paper: #f6f6f6;
    --ink: #333333;
    --ink-soft: #555555;
    --band: #8a96a1;
    --green: #8dc63f;
    --green-soft: #d7e7bf;
    --footer: #ececec;
    --sketch-a: #f1f1f1;
    --sketch-b: #dcdcdc;
  }
  * { margin: 0; padding: 0; box-sizing: border-box; }
  html, body { width: 1200px; height: 800px; overflow: hidden; background: var(--stage); }
  .flyer {
    position: absolute; left: 330px; top: 18px;
    width: 540px; height: 764px;
    background: var(--paper);
    box-shadow: 0 6px 18px rgba(0,0,0,.12);
    font-family: "EB Garamond", Georgia, serif;
    color: var(--ink);
    overflow: hidden;
  }
  .hero-visual {
    position: absolute; right: 0; top: 0; width: 250px; height: 222px;
    background: linear-gradient(160deg, var(--sketch-a) 0%, #e7e7e7 55%, var(--sketch-b) 100%);
  }
  .brand {
    position: absolute; left: 50px; top: 46px;
    display: flex; align-items: center; gap: 8px;
    font-family: "Sora", sans-serif; font-weight: 600; font-size: 11px;
    color: var(--ink-soft); letter-spacing: .02em;
  }
  .brand-dot { width: 9px; height: 9px; border-radius: 50%; background: var(--green); }
  .headline {
    position: absolute; left: 50px; top: 118px; width: 260px;
    font-family: "Sora", sans-serif; font-weight: 700;
    font-size: 17px; line-height: 1.32; color: #2b2b2b;
  }
  .tagline {
    position: absolute; left: 0; top: 222px; width: 100%; height: 24px;
    background: var(--band); color: #fff;
    font-family: "Open Sans", sans-serif; font-style: italic; font-size: 10.5px;
    line-height: 24px; padding-left: 52px;
  }
  .copy { position: absolute; left: 52px; width: 440px; font-size: 8.6px; line-height: 1.55; color: var(--ink-soft); }
  .copy p + p { margin-top: 3px; }
  .intro { top: 262px; }
  .section-title {
    position: relative; font-size: 13px; font-weight: 500; color: var(--ink);
    margin-bottom: 5px; padding-left: 4px;
  }
  .section-title::before {
    content: ""; position: absolute; left: -6px; top: -2px;
    width: 20px; height: 20px; border-radius: 50%;
    background: var(--green-soft); z-index: -1;
  }
  .block { position: absolute; isolation: isolate; }
  .block-team { left: 58px; top: 380px; width: 165px; }
  .block-time { left: 258px; top: 376px; width: 230px; }
  .block-more { left: 58px; top: 472px; width: 440px; }
  .block .copy { position: static; width: auto; }
  .contact-note { top: 556px; font-size: 9.2px; }
  .contact-note em { font-style: normal; color: var(--green); }
  .footer-strip {
    position: absolute; left: 0; top: 612px; width: 100%; height: 92px;
    background: var(--footer);
  }
  .photo { position: absolute; top: 604px; height: 100px; }
  .photo-house { left: 60px; width: 160px; background: linear-gradient(180deg, #cfd7de 0%, #d9d4cb 45%, #9d9a8c 100%); }
  .photo-reception { left: 236px; width: 160px; background: linear-gradient(180deg, #e2e0db 0%, #b08a5e 60%, #7d6a4b 100%); }
  .address {
    position: absolute; left: 418px; top: 624px;
    font-style: normal;
    font-size: 10px; line-height: 1.6; color: var(--ink-soft);
  }
  .address strong { font-weight: 600; color: var(--ink); }
  .label { color: var(--green); }
  .email { position: absolute; left: 66px; top: 728px; font-size: 10.5px; color: var(--ink-soft); }
</style>
</head>
<body>
  <article class="flyer">
    <div class="hero-visual" role="img" aria-label="Zarte Bleistiftskizze eines historischen Behandlungsraums mit Liege, Tisch und Stühlen"></div>

    <div class="brand"><span class="brand-dot"></span>Praxis Lindenhof</div>

    <h1 class="headline">Hausarztmedizin mit<br>Tiefe – dort, wo man<br>noch echte<br>Grundversorgung lebt</h1>

    <div class="tagline">Ein Ort, der trägt. Ein Team, das bleibt. Eine Arbeit, die Wertschätzung hat.</div>

    <div class="copy intro">
      <p>Manche Orte verändern die Art, wie man arbeitet. Unsere Praxis in Talwil ist so ein Ort.</p>
      <p>In einem historischen Gebäude gelegen, mit grosszügigem Ambiente, warmen Vertäfelungen und kunstvoller Wandbemalung, entstehen hier Behandlungsräume von Ruhe und Würde. Kein steriler Praxisalltag, sondern ein Ort, der Gespräche trägt und medizinische Arbeit unterstützt.</p>
      <p>Für diesen besonderen Ort suchen wir eine Hausärztin oder einen Hausarzt, die oder der nicht einfach einen Arbeitsplatz sucht, sondern einen Platz, an dem Medizin menschlich sein darf.</p>
    </div>

    <section class="block block-team">
      <h2 class="section-title">Ein Team mit Haltung</h2>
      <p class="copy">Sie arbeiten in einem freundlichen, über Jahre gewachsenen Team mit hoher personeller Kontinuität und geringer Fluktuation.</p>
    </section>

    <section class="block block-time">
      <h2 class="section-title">Zeit für gute Medizin</h2>
      <p class="copy">Unsere Patientinnen und Patienten sind überwiegend gut bis sehr gut situiert, wertschätzend und therapieoffen. Das ermöglicht ruhiges, strukturiertes Arbeiten mit Fokus auf Qualität, Beziehung und nachhaltige Behandlung.</p>
    </section>

    <section class="block block-more">
      <h2 class="section-title">Und sonst?</h2>
      <p class="copy">Der Praxisalltag ist klar strukturiert, ruhig und verlässlich. Geregelte und in Abstimmung flexible Arbeitszeiten ohne Wochenend- oder Nachtdienste, eine sehr gute leistungsbezogene Vergütung sowie ein respektvoller, wertschätzender Umgang auf Augenhöhe schaffen ein Umfeld, in dem man sich auf die medizinische Arbeit konzentrieren und langfristig wohlfühlen kann.</p>
    </section>

    <p class="copy contact-note">Wir freuen uns über eine unkomplizierte Kontaktaufnahme per <em>E-Mail oder Telefon</em> – gerne auch ganz unverbindlich und ohne vollständige Bewerbungsunterlagen.</p>

    <div class="footer-strip"></div>
    <div class="photo photo-house" role="img" aria-label="Foto des historischen Praxisgebäudes mit Vorplatz"></div>
    <div class="photo photo-reception" role="img" aria-label="Foto des Empfangs mit alter Holzkommode und Pflanzen"></div>

    <address class="address">
      <strong>Praxis Lindenhof</strong><br>
      Lindenweg 7<br>
      4712 Talwil<br>
      <span class="label">Tel:</span> 0620001234
    </address>

    <p class="email"><span class="label">E-Mail:</span> Helga.Weissmoor@praxis-lindenhof.ch</p>
  </article>
</body>
</html>
```